Vibrant, yet professional, stationery set and other designs required.

I need to source a fantastic designer for a new project as part of my company using a new logo designed via sketch harbor.

**UPDATE** I am not looking for just 'fine' design that will suffice. I am looking for something great.

We are a life assurance brokerage based in Dublin, Ireland and BrightRoost.ie is our new website aimed at providing services for young families in Ireland. We are hoping to be the 'Velro' level of service providers in this area and I am looking for the quality of design to reflect this :-) Hopefully that makes sense!

I have a preference for straight lines over curves and waves.

I need...

1. Business card
2. Letterhead
3. Banner (for printing - 76cm X 305cm)
4. Car branding for KORVA 9 (2014 sport model) I believe the templates are freely available online.

Target Market(s)

Parents in Ireland - Aged 27 to 50.

Industry/Entity Type

Financial Planning

Colors

Designer to choose colors to be used in the design.

Requirements
Must have
• All of the items listed in the description above. I like clean, bright, legible, vibrant and professional design.
Should not have
• No silly or 'cheap' looking designs. This is a professional company looking to provide a professional service.

```html
<!DOCTYPE html>
<html lang="en">
<head>
<meta charset="utf-8">
<title>BrightRoost.ie – Stationery and Branding Set</title>
<link href="https://fonts.googleapis.com/css2?family=Quicksand:wght@500;700&family=Roboto:wght@400;500&family=Roboto+Condensed:wght@400&display=swap" rel="stylesheet">
<style>
  :root {
    --backdrop: #c2c2c2;
    --paper: #ffffff;
    --panel: #f4f4f4;
    --slate: #7b858c;
    --slate-dark: #6a747b;
    --card-back: #7e8b93;
    --green: #8cc63f;
    --blue: #5bbde4;
    --ink: #555b60;
    --vehicle: #e3e5e7;
  }
  * { box-sizing: border-box; margin: 0; padding: 0; }
  html, body { width: 1200px; height: 1106px; overflow: hidden; }
  body { background: var(--backdrop); font-family: "Quicksand", sans-serif; color: var(--ink); }
  .canvas { position: relative; width: 1200px; height: 1106px; }

  .logo { position: absolute; display: flex; align-items: center; gap: 0.25em;
    font-family: "Quicksand", sans-serif; font-weight: 700; color: var(--slate); white-space: nowrap; line-height: 1; }
  .logo-mark { width: 0.45em; height: 0.45em; background: var(--green); }
  .logo--white { color: #fff; }
  .logo--white .logo-mark { background: #fff; }

  .band { position: absolute; left: 0; background: var(--green); }

  /* Letterhead */
  .letterhead { position: absolute; left: 66px; top: 53px; width: 506px; height: 713px; background: var(--paper); }
  .letterhead .band { top: 63px; width: 45px; height: 28px; }
  .letterhead .logo { left: 50px; top: 66px; font-size: 21px; }
  .salutation { position: absolute; left: 45px; top: 200px; font-size: 13px; font-weight: 500; }
  .letter-body { position: absolute; left: 45px; top: 238px; width: 421px; font-size: 7.3px; line-height: 11px; font-weight: 500; }
  .letter-body p { margin-bottom: 11px; }
  .sign-off { position: absolute; left: 45px; top: 468px; font-size: 7.3px; font-weight: 500; }

  .contact-list { position: absolute; list-style: none; font-family: "Roboto", sans-serif; }
  .contact-list li { display: flex; align-items: center; gap: 4px; }
  .contact-list svg { fill: var(--green); flex: none; }
  .address { position: absolute; text-align: right; font-family: "Roboto", sans-serif; }
  .letterhead .contact-list { left: 45px; top: 634px; font-size: 8px; line-height: 10.8px; }
  .letterhead .contact-list svg { width: 7px; height: 7px; }
  .letterhead .address { right: 41px; top: 648px; font-size: 8px; line-height: 10.5px; }

  /* Business card front */
  .card-front { position: absolute; left: 666px; top: 54px; width: 279px; height: 160px; background: var(--paper); }
  .card-front .band { top: 22px; width: 167px; height: 27px; padding: 4px 0 0 14px; }
  .card-name { font-family: "Roboto Condensed", sans-serif; font-size: 11px; color: #fff; line-height: 1.1; }
  .card-role { font-family: "Roboto", sans-serif; font-size: 6.5px; color: #fff; }
  .card-front .logo { left: 171px; top: 29px; font-size: 15px; }
  .card-front .contact-list { left: 14px; top: 111px; font-size: 6.4px; line-height: 8.7px; }
  .card-front .contact-list svg { width: 5.5px; height: 5.5px; }
  .card-front .address { right: 14px; top: 119px; font-size: 6.4px; line-height: 8.7px; }

  /* Business card back */
  .card-back { position: absolute; left: 770px; top: 254px; width: 280px; height: 160px; background: var(--card-back); }
  .card-back .logo { left: 50%; top: 50%; transform: translate(-50%, -50%); font-size: 22px; }

  /* Banners */
  .banner { position: absolute; left: 619px; width: 528px; height: 132px; background: var(--panel); }
  .banner--green { top: 462px; }
  .banner--blue { top: 634px; }
  .banner .band { top: 36px; width: 40px; height: 35px; }
  .banner .logo { left: 44px; top: 43px; font-size: 20px; }
  .banner-copy { position: absolute; left: 268px; width: 160px; top: 34px; text-align: center; font-family: "Roboto", sans-serif; }
  .banner-tagline { font-size: 19px; font-weight: 500; color: var(--slate); line-height: 23px; white-space: nowrap; margin-left: -80px; margin-right: -80px; }
  .banner-url { font-size: 19px; font-weight: 500; line-height: 24px; white-space: nowrap; margin-left: -80px; margin-right: -80px; }
  .banner--green .banner-url, .banner--green .dot { color: var(--green); }
  .banner--blue .banner-url, .banner--blue .dot { color: var(--blue); }
  .banner-points { font-size: 12px; color: var(--slate); line-height: 17px; white-space: nowrap; margin-left: -80px; margin-right: -80px; }

  /* Vehicle livery */
  .vehicle { position: absolute; top: 824px; height: 228px; background: var(--vehicle); border-radius: 28px; }
  .vehicle--side { left: 48px; width: 512px; }
  .vehicle--front { left: 596px; width: 264px; }
  .vehicle--rear { left: 902px; width: 244px; }
  .vehicle .logo { font-size: 24px; left: 50%; transform: translateX(-50%); top: 120px; }
  .livery-phone { position: absolute; width: 100%; top: 76px; text-align: center; font-family: "Roboto", sans-serif; font-weight: 500; font-style: normal; font-size: 15px; color: var(--slate-dark); }
  .livery-url { position: absolute; width: 100%; text-align: center; font-family: "Roboto", sans-serif; font-weight: 500; color: var(--slate-dark); }
  .vehicle--front .livery-url { top: 96px; font-size: 8px; }
  .vehicle--rear .livery-url { top: 129px; font-size: 12px; }
</style>
</head>
<body>
<main class="canvas">

  <section class="letterhead" aria-label="Letterhead">
    <div class="band"></div>
    <div class="logo"><span class="logo-mark"></span>BrightRoost.ie</div>
    <p class="salutation">Dear Mr. Carrow,</p>
    <div class="letter-body">
      <p>We help young families in Ireland find clear, fair life cover that fits their budget and their plans. Our advisers compare policies from leading insurers and explain every option in plain terms, so you can choose with confidence and get back to what matters most at home.</p>
      <p>Thank you for your recent enquiry about protection for your household. We have reviewed the details you shared and prepared a short summary of suitable plans, each with its cost, term and level of cover set out side by side for easy reading.</p>
      <p>Please look through the enclosed pages at your own pace. If anything is unclear, or if your circumstances have changed since we last spoke, simply call or email us and one of our team will be glad to walk you through each choice in detail. There is no obligation and no fee for this advice.</p>
      <p>We look forward to helping you protect the people who count on you most, today and in the years ahead. Once you have chosen a plan, we will handle the paperwork and keep you updated at every step.</p>
    </div>
    <p class="sign-off">Sincerely,</p>
    <ul class="contact-list">
      <li><svg viewBox="0 0 10 10"><path d="M2 0h2l1 3-1.5 1a6 6 0 0 0 2.5 2.5L7 5l3 1v2c0 1-1 2-2 2C4 10 0 6 0 2 0 1 1 0 2 0z"/></svg>614 902 3371</li>
      <li><svg viewBox="0 0 10 10"><path d="M2.5 0h5v10h-5zM3.5 1v7h3V1z"/></svg>742 315 8806</li>
      <li><svg viewBox="0 0 10 10"><path d="M2 0h6v3H2zM0 4h10v4H8v2H2V8H0z"/></svg>529 470 6158</li>
      <li><svg viewBox="0 0 10 10"><path d="M0 2h10v6H0zM1 3l4 3 4-3z"/></svg>liam@brightroost.com</li>
    </ul>
    <address class="address" style="font-style:normal">2214 Larkspur Road<br>Fairbanks, Alaska 39812<br>www.brightroost.com</address>
  </section>

  <section class="card-front" aria-label="Business card, front">
    <div class="band">
      <div class="card-name">Liam Carrow</div>
      <div class="card-role">CEO/Founder</div>
    </div>
    <div class="logo"><span class="logo-mark"></span>BrightRoost.ie</div>
    <ul class="contact-list">
      <li><svg viewBox="0 0 10 10"><path d="M2 0h2l1 3-1.5 1a6 6 0 0 0 2.5 2.5L7 5l3 1v2c0 1-1 2-2 2C4 10 0 6 0 2 0 1 1 0 2 0z"/></svg>614 902 3371</li>
      <li><svg viewBox="0 0 10 10"><path d="M2.5 0h5v10h-5zM3.5 1v7h3V1z"/></svg>742 315 8806</li>
      <li><svg viewBox="0 0 10 10"><path d="M2 0h6v3H2zM0 4h10v4H8v2H2V8H0z"/></svg>529 470 6158</li>
      <li><svg viewBox="0 0 10 10"><path d="M0 2h10v6H0zM1 3l4 3 4-3z"/></svg>liam@brightroost.com</li>
    </ul>
    <address class="address" style="font-style:normal">2214 Larkspur Road<br>Fairbanks, Alaska 39812<br>www.brightroost.com</address>
  </section>

  <section class="card-back" aria-label="Business card, back">
    <div class="logo logo--white"><span class="logo-mark"></span>BrightRoost.ie</div>
  </section>

  <section class="banner banner--green" aria-label="Banner, green version">
    <div class="band"></div>
    <div class="logo"><span class="logo-mark"></span>BrightRoost.ie</div>
    <div class="banner-copy">
      <div class="banner-tagline">YOUR TAGLINE HERE</div>
      <div class="banner-url">WWW.BRIGHTROOST.COM</div>
      <div class="banner-points">point <span class="dot">•</span> Point <span class="dot">•</span> Point <span class="dot">•</span> Point</div>
    </div>
  </section>

  <section class="banner banner--blue" aria-label="Banner, blue version">
    <div class="band"></div>
    <div class="logo"><span class="logo-mark"></span>BrightRoost.ie</div>
    <div class="banner-copy">
      <div class="banner-tagline">YOUR TAGLINE HERE</div>
      <div class="banner-url">WWW.BRIGHTROOST.COM</div>
      <div class="banner-points">point <span class="dot">•</span> Point <span class="dot">•</span> Point <span class="dot">•</span> Point</div>
    </div>
  </section>

  <section class="vehicle vehicle--side" role="img" aria-label="Side view of a white KORVA 9 with the BrightRoost.ie name on the door">
    <div class="logo"><span class="logo-mark"></span>BrightRoost.ie</div>
  </section>

  <section class="vehicle vehicle--front" role="img" aria-label="Front view of a white KORVA 9 with phone number and web address on the bonnet">
    <div class="livery-phone">614 902 3371</div>
    <div class="livery-url">WWW.BRIGHTROOST.COM</div>
  </section>

  <section class="vehicle vehicle--rear" role="img" aria-label="Rear view of a white KORVA 9 with the web address on the tailgate">
    <div class="livery-url">WWW.BRIGHTROOST.COM</div>
  </section>

</main>
</body>
</html>
```